Business card for denture clinic Veltrimora

We need a new business card with our new logo. We are a denture clinic in New Zealand with our target market being 45+ years old. We would need a space on the back to write our patients next appointment on. We would space for only one appointment rather than a list. We will attach a photo showing an example of this. But of course, we would like to see your twist on this. We want it to be bold and easy to read and a good mixture of professional but modern. We have attached our logo to be used on the card.

Target Market(s)

People aged 45+ needing dentures

Industry/Entity Type

Dental

Contact Information for Business Card

We want our logo on the front and the space to write an appointment on the back. I've attached an example our our old business card showing this. We need to have the technicians details on the front.

Font styles to use
Sans Serif

Colors
0255a3
919191
fbfbfb

Requirements
Must have
• The following details:
• Liam Dorsett BDT, PGDipCDentTech Calverin
• Dental Prosthetist
• Phone numbers: 0800 47 3125
• 09 572 1394
• Email: liam@veltrimora.co.nz
• www.veltrimora.co.nz
• Address: 14 Marlow Crest Road
• Halbrook West
• Auckland 0793
Nice to have
• We would like our business cards to have more than just two colours as we want them to be more vibrant. We have uploaded an example of a business card we liked that showed this.

```html
<!DOCTYPE html>
<html lang="en">
<head>
<meta charset="utf-8">
<title>Veltrimora Business Card</title>
<link rel="stylesheet" href="https://fonts.googleapis.com/css2?family=Open+Sans:ital,wght@0,400;0,600;1,400&display=swap">
<style>
  :root {
    --brand-blue: #0a6fba;
    --brand-blue-deep: #0255a3;
    --swoosh-grey: #767072;
    --text-grey: #5f5f5f;
    --rule-grey: #919191;
    --card-white: #fbfbfb;
    --field-fill: #f4f4f4;
    --backdrop: #ebe8e3;
  }
  * { box-sizing: border-box; margin: 0; padding: 0; }
  html, body {
    width: 1200px; height: 987px; overflow: hidden;
    background: var(--backdrop);
    font-family: "Open Sans", Arial, sans-serif;
  }
  .stage { position: relative; width: 1200px; height: 987px; }

  .card {
    position: absolute; left: 293px; width: 615px; height: 352px;
    border-radius: 22px; overflow: hidden;
    box-shadow: 0 3px 8px rgba(0,0,0,0.18);
  }
  .card--front { top: 130px; background: var(--card-white); }
  .card--back { top: 505px; background: var(--brand-blue); }

  /* Brand lockup */
  .brand { position: absolute; display: flex; flex-direction: column; align-items: center; }
  .brand__square { width: 55px; height: 55px; background: var(--brand-blue); }
  .brand__name {
    margin-top: 8px; font-weight: 400; font-size: 30px; letter-spacing: 1.5px;
    color: var(--brand-blue); line-height: 1; text-transform: uppercase;
  }
  .card--front .brand { right: 23px; top: 29px; }
  .card--back .brand { left: 0; right: 0; top: 53px; }
  .card--back .brand__square { width: 57px; height: 57px; background: var(--card-white); }
  .card--back .brand__name { color: #fff; margin-top: 10px; }

  /* Technician details */
  .tech { position: absolute; left: 33px; top: 163px; }
  .tech__name { font-size: 21px; font-weight: 600; color: var(--brand-blue); line-height: 1; }
  .tech__creds { font-size: 16px; }
  .tech__role { margin-top: 7px; font-size: 16px; color: var(--text-grey); line-height: 1; }
  .rule { position: absolute; left: 32px; top: 216px; width: 560px; height: 1px; background: var(--rule-grey); }

  .contact, .address {
    position: absolute; top: 226px; font-size: 15px; line-height: 23.5px; color: var(--text-grey);
  }
  .contact { left: 33px; }
  .contact__label { color: var(--brand-blue); font-weight: 600; }
  .address { right: 23px; text-align: right; }

  .wave { position: absolute; left: 0; top: 0; }

  /* Appointment side */
  .appointment__title {
    position: absolute; left: 0; right: 0; top: 204px; text-align: center;
    font-size: 23px; font-weight: 600; color: #fff;
  }
  .field {
    position: absolute; top: 273px; width: 239px; height: 42px; border-radius: 21px;
    background: var(--field-fill); padding-left: 17px;
    font-size: 17px; font-style: italic; color: var(--brand-blue); line-height: 42px;
  }
  .field--date { left: 29px; }
  .field--time { left: 345px; }
</style>
</head>
<body>
<main class="stage">
  <section class="card card--front" aria-label="Business card front">
    <div class="brand">
      <div class="brand__square"></div>
      <div class="brand__name">Veltrimora</div>
    </div>

    <div class="tech">
      <p class="tech__name">LIAM DORSETT <span class="tech__creds">BDT, PGDipCDentTech Calverin</span></p>
      <p class="tech__role">Dental Prosthetist</p>
    </div>
    <div class="rule"></div>

    <div class="contact">
      <p><span class="contact__label">P :</span> 0800 47 3125</p>
      <p><span class="contact__label">C :</span> 09 572 1394</p>
      <p>liam@veltrimora.co.nz</p>
    </div>
    <div class="address">
      <p>14 Marlow Crest Road</p>
      <p>Halbrook West, Auckland 0793</p>
      <p>www.veltrimora.co.nz</p>
    </div>

    <svg class="wave" width="615" height="352" viewBox="0 0 615 352" aria-hidden="true">
      <path d="M0,342 C160,358 430,362 615,296 L615,352 L0,352 Z" fill="var(--brand-blue)"/>
      <path d="M6,333 C70,316 190,310 320,326 C440,340 540,326 604,290 C560,326 440,346 320,341 C200,336 90,328 6,337 Z" fill="var(--swoosh-grey)"/>
    </svg>
  </section>

  <section class="card card--back" aria-label="Business card back">
    <div class="brand">
      <div class="brand__square"></div>
      <div class="brand__name">Veltrimora</div>
    </div>
    <h2 class="appointment__title">Next Appointment</h2>
    <div class="field field--date">date:</div>
    <div class="field field--time">time:</div>
  </section>
</main>
</body>
</html>
```